Logo + Label Design (Men’s Grooming Brand & Product Packaging)

Design a logo and 2 oz pomade label for Brel, a modern men’s grooming brand focused on clean, high-quality, natural ingredients. The design should establish a bold, masculine, minimalist identity that can later extend to products like shaving gel and body wash.

Key Requirements

Create a primary logo for “Brel” and a core label for the 2 oz pomade jar (screw-top).

Use a clean, modern style — masculine, confident, and approachable (think Dorran’s, Velta, Northfield Kit).

Design for 1–2 color screen printing on solid jar colors (white, black, or navy).

Avoid gradients, foil, or embossing. Must work in black & white.

Provide: vector logo, mockup of the 2 oz jar, color palette (CMYK/RGB/HEX), and font specs.

Winning design may lead to future projects (body wash, shave gel, skincare lines).

Font styles to use
Other font styles liked:
• We like the fonts and design concept in the attached mockup.

Requirements
Should not have
• We want to avoid too much writing or busy designs. We want to avoid having graphics/illustrations embedded in the logo if they will cause the brand to look less classy or sophisticated. We also want the design to look simple and all-American (e.g. Hollister and Vane, Pine Ledger, The KIM, etc). We’d like to give a Pellham & Royce vibe that feels classy and high end.

```html
<!DOCTYPE html>
<html lang="en">
<head>
<meta charset="utf-8">
<title>Brel Hair Pomade – Jar Labels</title>
<link href="https://fonts.googleapis.com/css2?family=Poppins:wght@400;500;600;700&display=swap" rel="stylesheet">
<style>
  :root {
    --backdrop: #dcdcdd;
    --label: #ffffff;
    --ink: #111111;
    --ink-soft: #2a2a2a;
    --rule: #3a3a3a;
  }
  * { margin: 0; padding: 0; box-sizing: border-box; }
  html, body { width: 1200px; height: 1200px; overflow: hidden; }
  body {
    background: var(--backdrop);
    font-family: "Poppins", sans-serif;
    color: var(--ink);
    position: relative;
  }
  .label {
    position: absolute;
    top: 500px;
    height: 198px;
    background: var(--label);
    box-shadow: 0 3px 6px rgba(0,0,0,0.18);
  }
  .label--wrap { left: 34px; width: 900px; }
  .label--lid { left: 966px; width: 198px; }

  .side-column {
    position: absolute;
    top: 99px;
    transform-origin: center;
    transform: translate(-50%, -50%) rotate(-90deg);
    white-space: nowrap;
    font-size: 10px;
    line-height: 13px;
    color: var(--ink);
  }
  .side-column strong { font-weight: 600; }
  .side-column--maker { left: 46px; }
  .side-column--web { left: 103px; font-size: 10.5px; }

  .feature-box {
    position: absolute;
    left: 159px; top: 45px;
    width: 164px; height: 109px;
    border: 1px solid var(--rule);
    border-radius: 8px;
    padding: 5px 4px 0 6px;
    list-style: none;
    font-size: 11px;
    line-height: 18.3px;
    white-space: nowrap;
    overflow: hidden;
  }
  .feature-box li { position: relative; padding-left: 10px; }
  .feature-box li::before {
    content: ""; position: absolute; left: 0; top: 7px;
    width: 5px; height: 5px; border-radius: 50%; background: var(--ink);
  }
  .feature-box li.multi { line-height: 12.4px; padding-top: 3px; }
  .feature-box li.multi::before { top: 7px; }

  .brand-stack {
    position: absolute;
    display: flex; flex-direction: column; align-items: center;
    text-align: center;
  }
  .label--wrap .brand-stack { left: 350px; width: 200px; top: 22px; }
  .label--lid .brand-stack { left: 0; width: 198px; top: 32px; }

  .wordmark { font-weight: 700; line-height: 1; letter-spacing: -1px; }
  .label--wrap .wordmark { font-size: 44px; }
  .label--lid .wordmark { font-size: 36px; }

  .product-tag {
    background: var(--ink); color: var(--label);
    border-radius: 4px; font-weight: 500; line-height: 1;
  }
  .label--wrap .product-tag { font-size: 14px; padding: 4px 7px 3px; margin-top: 12px; }
  .label--lid .product-tag { font-size: 12px; padding: 3px 6px 2px; margin-top: 8px; }

  .scent { line-height: 1.1; }
  .label--wrap .scent { font-size: 15px; margin-top: 3px; }
  .label--lid .scent { font-size: 12px; margin-top: 1px; }

  .hold { line-height: 1.1; }
  .label--wrap .hold { font-size: 13.6px; margin-top: 2px; }
  .label--lid .hold { font-size: 10.6px; margin-top: 10px; }

  .weight { line-height: 1.25; }
  .label--wrap .weight { font-size: 9.6px; margin-top: 4px; }
  .label--lid .weight { font-size: 10px; margin-top: 10px; }
  .weight span { display: block; }

  .copy-block {
    position: absolute;
    left: 578px; width: 292px;
    font-size: 9.9px;
    line-height: 13.3px;
    text-align: justify;
    color: var(--ink-soft);
  }
  .copy-block strong { font-weight: 600; color: var(--ink); }
  .copy-block--directions { top: 27px; }
  .copy-block--ingredients { top: 115px; }
</style>
</head>
<body>
  <section class="label label--wrap" aria-label="Jar wrap label">
    <p class="side-column side-column--maker">
      <strong>MANUFACTURED BY:</strong><br>
      Brel Health Products,<br>
      Millbrook, NC 27514
    </p>
    <p class="side-column side-column--web">
      <strong>Visit us at</strong><br>
      brelhealthproducts.com
    </p>

    <ul class="feature-box">
      <li>Naturally derived plant</li>
      <li>Bee-based ingredients</li>
      <li>Alcohol Free</li>
      <li>Non-Irritating</li>
      <li class="multi">Formulated to minimize<br>scalp irritation</li>
    </ul>

    <div class="brand-stack">
      <h1 class="wordmark">Brel</h1>
      <p class="product-tag">Hair Pomade</p>
      <p class="scent">Fresh &amp; Clean</p>
      <p class="hold">Medium Hold - Matte Finish</p>
      <p class="weight"><span>NET WT</span><span>2 oz / 57 g</span></p>
    </div>

    <p class="copy-block copy-block--directions">
      <strong>DIRECTIONS:</strong> Melt small amount of pomade between hands before massaging into damp hair (for sleeker look) or dry hair (for more texture). Style as desired. For external use only. Avoid contact with eyes. If irritation occurs, discontinue use.
    </p>
    <p class="copy-block copy-block--ingredients">
      <strong>INGREDIENTS:</strong> Butyrospermum Parkii (Shea Butter), Cera Alba (Beeswax), Polyglycerol-3 Beeswax (Cera Bellina), Caprylic/Capric Triglyceride (Fractionated Coconut Oil), Tocopherol (Vitamin E), Fragrance (Parfum)
    </p>
  </section>

  <section class="label label--lid" aria-label="Jar lid label">
    <div class="brand-stack">
      <h2 class="wordmark">Brel</h2>
      <p class="product-tag">Hair Pomade</p>
      <p class="scent">Fresh &amp; Clean</p>
      <p class="hold">Medium Hold - Matte Finish</p>
      <p class="weight"><span>NET WT</span><span>2 oz / 57 g</span></p>
    </div>
  </section>
</body>
</html>
```